UK Online Auction Site needs a clever design

We need a contemporary landing page and registration page design for a UK auction website, that look equally at home on PC's and tablets . The design should be fresh, bright, clean, professional, robust, and familiar. We would like to see something clever but functional.

Online

```html
<!DOCTYPE html>
<html lang="en">
<head>
<meta charset="utf-8">
<title>Bidwell – UK Online Auctions</title>
<link rel="stylesheet" href="https://fonts.googleapis.com/css2?family=Roboto+Condensed:wght@300;400;700&family=Open+Sans:wght@400;600&display=swap">
<style>
:root{
  --blue:#1a8fd6;
  --blue-dark:#0f6fb3;
  --blue-light:#2fa3e6;
  --orange:#f7a100;
  --green:#8cc414;
  --ink:#333;
  --muted:#555;
  --bg:#f8f7f9;
  --footer:#1e1e1e;
  --footer-text:#ddd;
}
*{box-sizing:border-box;margin:0;padding:0}
html,body{width:960px;height:1200px;overflow:hidden}
body{background:var(--bg);font-family:"Open Sans",sans-serif;color:var(--ink);position:relative}
.page{position:absolute;left:0;top:0;width:960px;height:1200px}

/* header */
.brand{position:absolute;left:122px;top:20px;display:flex;align-items:center;gap:8px;
  font-family:"Roboto Condensed",sans-serif;font-weight:700;font-size:34px;color:var(--blue)}
.brand-dot{width:14px;height:14px;border-radius:50%;background:var(--blue)}
.nav{position:absolute;top:36px;left:403px;display:flex;align-items:center;
  font-family:"Roboto Condensed",sans-serif;font-size:12.5px;color:#444}
.nav-item{display:flex;align-items:center;gap:5px;padding:0 7px;border-right:1px solid #ddd;height:14px}
.nav-item:last-child{border-right:0}
.nav-item svg{width:11px;height:11px;fill:#444}
.sell-btn{background:var(--blue);color:#fff;border-radius:12px;height:23px;padding:0 12px;border:0;margin-right:6px}
.sell-btn svg{fill:#fff}
.caret{font-size:7px}
.register{position:absolute;left:762px;top:36px;width:76px;height:22px;border-radius:11px;background:var(--green);
  color:#fff;font-family:"Roboto Condensed",sans-serif;font-size:11.5px;display:flex;align-items:center;justify-content:center;gap:5px}
.register svg{width:10px;height:10px;fill:#fff}

/* search */
.searchbar{position:absolute;left:122px;top:87px;width:717px;height:40px;
  background:linear-gradient(#2b9fe4,var(--blue-dark));border-radius:2px}
.search-field{position:absolute;left:36px;top:6px;width:510px;height:28px;background:#fff;border-radius:14px;
  display:flex;font-family:"Roboto Condensed",sans-serif;font-size:10px;color:#444;align-items:center}
.cat-select{width:154px;padding:0 13px;border-right:1px solid #ddd;height:100%;display:flex;align-items:center;justify-content:space-between}
.query{padding-left:14px}
.search-btn{position:absolute;left:561px;top:6px;width:120px;height:29px;border-radius:15px;background:var(--orange);
  color:#fff;font-family:"Roboto Condensed",sans-serif;font-size:15px;display:flex;align-items:center;justify-content:center;gap:6px}
.search-btn svg{width:13px;height:13px}

/* headings */
.section-title{position:absolute;left:0;width:960px;text-align:center;font-family:"Roboto Condensed",sans-serif;
  font-weight:300;font-size:39px;color:var(--blue);line-height:1}
.section-title b{font-weight:700}
.intro-title{top:169px}

/* intro */
.intro-photo{position:absolute;left:149px;top:236px;width:313px;height:172px;
  background:linear-gradient(120deg,#f6c8d8,#e9b9a8 45%,#f4d4e0)}
.intro-text{position:absolute;left:493px;top:236px;width:312px}
.intro-text h2{font-family:"Roboto Condensed",sans-serif;font-weight:300;font-size:17px;color:var(--blue);margin-bottom:6px}
.intro-text p{font-size:10.4px;line-height:15.5px;color:var(--muted)}
.learn-btn{position:absolute;left:493px;top:382px;width:100px;height:23px;border-radius:12px;background:var(--green);
  color:#fff;font-size:9.5px;display:flex;align-items:center;justify-content:center;gap:5px}

.products-title{top:460px}
.products-lead{position:absolute;top:503px;left:0;width:960px;text-align:center;font-size:11.5px;color:#444}

/* tiles */
.grid{position:absolute;left:121px;top:554px;display:grid;grid-template-columns:repeat(4,170px);grid-auto-rows:218px;column-gap:13.5px;row-gap:15px}
.tile{position:relative;overflow:hidden}
.tile-photo{position:absolute;inset:0}
.tile-label{position:absolute;left:0;right:0;bottom:0;height:47px;background:rgba(20,20,20,.78);color:#fff;text-align:center;padding-top:7px}
.tile-label h3{font-weight:600;font-size:13px;line-height:16px}
.tile-label span{font-size:8px}
.fashion{background:linear-gradient(#5a5a5a,#2c2c2c 60%,#c9473f)}
.home{background:linear-gradient(#7fae4a,#a9b09a 45%,#4f7a30)}
.collect{background:linear-gradient(90deg,#e9e6e1,#f7f6f3 50%,#c9c2b4)}
.jewel{background:linear-gradient(#f4e6ee,#c99a7d 60%,#2e8f88)}
.toy{background:linear-gradient(#e6cc96,#f3f0ea 50%,#d9b66e)}
.sport{background:linear-gradient(#4aa6d9,#2b2b2b 40%,#6a5a44)}
.motors{background:linear-gradient(#6b6b6b,#2a2a2a 50%,#111)}
.tile-feature{background:linear-gradient(#1f9be0,#1585cc);color:#fff;text-align:center;padding:40px 10px 0}
.tile-feature .feature-brand{font-family:"Open Sans",sans-serif;font-weight:600;font-size:22px;margin-bottom:10px}
.tile-feature h3{font-weight:600;font-size:13.5px;margin-bottom:5px}
.tile-feature p{font-size:8.6px;line-height:12px;margin-bottom:10px}
.tile-feature .outline-btn{display:inline-block;border:1px solid #fff;padding:4px 10px;font-size:8px}

/* footer */
.footer{position:absolute;left:0;top:1046px;width:960px;height:154px;background:var(--footer);color:var(--footer-text)}
.footer h4{font-family:"Roboto Condensed",sans-serif;font-weight:400;font-size:12px;color:#fff;margin-bottom:8px}
.footer-col{position:absolute;top:24px;font-size:8.5px}
.footer-col ul{list-style:none}
.footer-col li{line-height:17.5px}
.sitemap ul{display:grid;grid-template-columns:70px 60px}
.col-sitemap{left:123px}
.col-buy{left:298px}
.col-sell{left:416px}
.col-follow{left:558px;top:20px}
.social li{display:flex;align-items:center;gap:10px;height:26px;font-size:9px}
.social i{width:20px;height:20px;display:block;border-radius:2px}
.sq-a{background:#3b5a98}.sq-b{background:#2aa7df}.sq-c{background:#d84130}
.footer-brand{position:absolute;left:705px;top:20px;width:133px;text-align:center;font-weight:600;font-size:30px;color:#555}
.copyright{position:absolute;left:690px;top:88px;width:148px;text-align:right;font-size:9px;line-height:11.5px}
</style>
</head>
<body>
<div class="page">

  <header>
    <div class="brand"><span class="brand-dot"></span>Bidwell</div>
    <nav class="nav">
      <span class="nav-item sell-btn"><svg viewBox="0 0 10 10"><path d="M0 0h5l5 5-5 5-5-5zM2 2v1h1V2z"/></svg>Sell <span class="caret">▼</span></span>
      <span class="nav-item"><svg viewBox="0 0 10 10"><circle cx="5" cy="3" r="2.5"/><path d="M0 10c0-4 10-4 10 0z"/></svg>Sign Up <span class="caret">▼</span></span>
      <span class="nav-item"><svg viewBox="0 0 10 10"><path d="M0 3h10l-1.5 7h-7zM3 3l2-3 2 3"/></svg>Basket <span class="caret">▼</span></span>
      <span class="nav-item"><svg viewBox="0 0 10 10"><circle cx="5" cy="5" r="5"/></svg>Help</span>
      <span class="nav-item"><svg viewBox="0 0 10 10"><path d="M0 2h10v6H0z"/></svg>Contact</span>
    </nav>
    <div class="register"><svg viewBox="0 0 10 10"><circle cx="5" cy="3" r="2.5"/><path d="M0 10c0-4 10-4 10 0z"/></svg>Register</div>
  </header>

  <div class="searchbar">
    <div class="search-field">
      <div class="cat-select">All Categories <span class="caret">▼</span></div>
      <div class="query">Search for a brand,product or specific item</div>
    </div>
    <div class="search-btn"><svg viewBox="0 0 14 14"><circle cx="5.5" cy="5.5" r="4" fill="none" stroke="#fff" stroke-width="2"/><path d="M8.5 8.5l4 4" stroke="#fff" stroke-width="2.4"/></svg>Search</div>
  </div>

  <h1 class="section-title intro-title"><b>Hi There</b> Nice to meet you</h1>

  <div class="intro-photo" role="img" aria-label="Photo of three models with long hair on a pink background"></div>
  <div class="intro-text">
    <h2>Lets talk about Bidwell</h2>
    <p>It is a long established fact that a reader will be distracted by the readable content of a page when looking at its layout. The point of using Lorem Ipsum is that it has a more-or-less normal distribution of letters, as opposed to using 'Content here, content here', making it look like readable English. Many desktop publishing packages and web page editors now use Lorem Ipsum as their default model text.</p>
  </div>
  <div class="learn-btn">Learn More <span>⟶</span></div>

  <h2 class="section-title products-title"><b>Top</b> Products</h2>
  <p class="products-lead">It is a long established fact that a reader will be distracted by the readable content.</p>

  <div class="grid">
    <div class="tile"><div class="tile-photo fashion" role="img" aria-label="Fashion model in sunglasses and scarf on a runway"></div><div class="tile-label"><h3>Fashion</h3><span>See All Product →</span></div></div>
    <div class="tile"><div class="tile-photo home" role="img" aria-label="House with garden and trees"></div><div class="tile-label"><h3>Home &amp; Garden</h3><span>See All Product →</span></div></div>
    <div class="tile tile-feature">
      <div class="feature-brand">Bidwell</div>
      <h3>Electricals &amp; Technology</h3>
      <p>It is a long established fact that a reader will be distracted by the readable content</p>
      <span class="outline-btn">See All Product →</span>
    </div>
    <div class="tile"><div class="tile-photo collect" role="img" aria-label="Antique bathroom with tub and chandelier"></div><div class="tile-label"><h3>Collectables &amp; Aniques</h3><span>See All Product →</span></div></div>
    <div class="tile"><div class="tile-photo jewel" role="img" aria-label="Woman wearing traditional jewellery"></div><div class="tile-label"><h3>Jewellery &amp; Beauty</h3><span>See All Product →</span></div></div>
    <div class="tile"><div class="tile-photo toy" role="img" aria-label="White teddy bear with bow tie"></div><div class="tile-label"><h3>Toy</h3><span>See All Product →</span></div></div>
    <div class="tile"><div class="tile-photo sport" role="img" aria-label="Bowling ball and pins in a bowling alley"></div><div class="tile-label"><h3>Sport &amp; Leisure</h3><span>See All Product →</span></div></div>
    <div class="tile"><div class="tile-photo motors" role="img" aria-label="Black sports motorcycle"></div><div class="tile-label"><h3>Motors</h3><span>See All Product →</span></div></div>
  </div>

  <footer class="footer">
    <div class="footer-col col-sitemap sitemap"><h4>Site Map</h4>
      <ul><li>Contact</li><li>About</li><li>Terms</li><li>News</li><li>Privacy</li><li>Feeds</li><li>RSS</li></ul></div>
    <div class="footer-col col-buy"><h4>Buy</h4>
      <ul><li>Categories</li><li>Search</li><li>Currency</li><li>Converter</li></ul></div>
    <div class="footer-col col-sell"><h4>Sell</h4>
      <ul><li>Sell New Item</li><li>Sell Bulk Items</li></ul></div>
    <div class="footer-col col-follow"><h4>Follow Us</h4>
      <ul class="social"><li><i class="sq-a"></i>Circlebook</li><li><i class="sq-b"></i>Chirper</li><li><i class="sq-c"></i>Orbit+</li></ul></div>
    <div class="footer-brand">Bidwell</div>
    <p class="copyright">Copyright Bidwell ® 2003-13. All rights reserved</p>
  </footer>

</div>
</body>
</html>
```